Business Card Design for Flood Rescue 360 - Property Restoration Professionals

I need a business card designed for Flood Rescue 360. We are a full-service property restoration solution. Providing water, fire, smoke & storm restoration as well as mold remediation and full remodel or reconstruction to homes and businesses across Dallas-Fort Worth, TX.
Target Market(s)
home and business owners with insurance covered property damage from water, fire or storm related damage
Industry/Entity Type
property restoration
Contact Information for Business Card
Marcus Pelley General Manager Cell: 214-555-0193 Office: 469-555-0148 email: Marcus@FloodRescue360.example services: Water, Fire, Mold, Reconstruction Tagline: Urgency for Your Water Emergency!
Look and feel
Each slider illustrates characteristics of the customer's brand and the style your logo design should communicate.

```html
<!DOCTYPE html>
<html lang="en">
<head>
<meta charset="utf-8">
<title>Flood Rescue 360 – Business Card</title>
<link rel="stylesheet" href="https://fonts.googleapis.com/css2?family=Montserrat:wght@400;500;700;800&display=swap">
<style>
  :root {
    --backdrop: #4a4a4a;
    --card: #141414;
    --cyan: #00aeef;
    --white: #f2f2f2;
    --grey: #8a8a8a;
  }
  * { margin: 0; padding: 0; box-sizing: border-box; }
  html, body { width: 1200px; height: 801px; overflow: hidden; }
  body {
    background: var(--backdrop);
    font-family: "Montserrat", Arial, sans-serif;
    color: var(--white);
    position: relative;
  }
  .card {
    position: absolute;
    left: 290px;
    width: 620px;
    height: 354px;
    background: var(--card);
    overflow: hidden;
    box-shadow: 0 12px 30px rgba(0,0,0,.45);
  }
  .card--front { top: 30px; border-bottom: 3px solid var(--cyan); border-right: 3px solid var(--cyan); }
  .card--back { top: 416px; border-bottom: 3px solid var(--cyan); border-left: 3px solid var(--cyan); }

  /* company name */
  .company-name {
    position: absolute;
    color: var(--white);
    font-weight: 500;
    white-space: nowrap;
    line-height: 1;
  }
  .card--front .company-name { right: 28px; top: 40px; font-size: 28px; }
  .card--back .company-name { left: 50%; top: 50%; transform: translate(-50%, -50%); font-size: 26px; }

  /* services */
  .services { position: absolute; right: 28px; top: 148px; text-align: right; }
  .services__title { color: var(--cyan); font-weight: 800; font-size: 22px; letter-spacing: 1px; margin-bottom: 6px; }
  .services__list { list-style: none; font-size: 15px; line-height: 1.45; }
  .services__list li::after {
    content: ""; display: inline-block; width: 7px; height: 7px; margin-left: 7px;
    background: var(--cyan); vertical-align: middle;
  }

  /* person block */
  .accent-bar { position: absolute; left: 0; top: 168px; width: 16px; height: 46px; background: var(--cyan); }
  .person { position: absolute; left: 36px; top: 160px; }
  .person__name { color: var(--cyan); font-weight: 700; font-size: 30px; line-height: 1.1; }
  .person__title { font-size: 16px; margin-top: 2px; }
  .tagline { font-size: 15px; margin-top: 14px; }
  .contact { list-style: none; margin-top: 12px; font-size: 14px; line-height: 1.45; }
  .contact li { display: flex; align-items: center; gap: 8px; }
  .contact svg { width: 13px; height: 13px; fill: var(--cyan); flex: none; }

  /* back */
  .back-texture {
    position: absolute; inset: 0;
    background: linear-gradient(100deg, #3a3a3a 0%, #222 35%, #161616 65%, #0e0e0e 100%);
  }
</style>
</head>
<body>

<section class="card card--front" aria-label="Business card front">
  <p class="company-name">Flood Rescue 360</p>

  <div class="services">
    <h2 class="services__title">SERVICES</h2>
    <ul class="services__list">
      <li>Water</li>
      <li>Fire</li>
      <li>Mold</li>
      <li>Reconstruction</li>
    </ul>
  </div>

  <div class="accent-bar"></div>
  <div class="person">
    <h1 class="person__name">Marcus Pelley</h1>
    <p class="person__title">General Manager</p>
    <p class="tagline">Urgency for Your Water Emergency!</p>
    <ul class="contact">
      <li><svg viewBox="0 0 16 16" aria-hidden="true"><path d="M4 1h8v14H4zM5.5 2.5v10h5v-10z"/></svg>214-555-0193</li>
      <li><svg viewBox="0 0 16 16" aria-hidden="true"><path d="M2 5c0-2 12-2 12 0v2h-3V6H5v1H2zM4 8h8l2 6H2z"/></svg>469-555-0148</li>
      <li><svg viewBox="0 0 16 16" aria-hidden="true"><path d="M1 4h14v9H1zM2.5 5.5 8 9.5l5.5-4v6h-11z"/></svg>Marcus@FloodRescue360.example</li>
      <li><svg viewBox="0 0 16 16" aria-hidden="true"><circle cx="8" cy="8" r="7"/></svg>FloodRescue360.example</li>
    </ul>
  </div>
</section>

<section class="card card--back" aria-label="Business card back">
  <div class="back-texture" role="img" aria-label="Glossy black background with an embossed repeating pattern"></div>
  <p class="company-name">Flood Rescue 360</p>
</section>

</body>
</html>
```